Corvena Hotel, city center modern minimal hotel operating all year round, on Rhodes island Greece

city, modern ,all year operating hotel

Target Market(s)

tourists, business agents

Industry/Entity Type

tourism

Number of Pages Required

2 page

Requirements
Must have
• room type photos and descriptions, amenities individual listing (graphic), comments sections, map driving location details
Nice to have
• gallery section, modern and minimal design, amenities section, individual room type descriptions, photos and facilities

```html
<!DOCTYPE html>
<html lang="en">
<head>
<meta charset="utf-8">
<title>Corvena Hotel</title>
<link href="https://fonts.googleapis.com/css2?family=Cinzel:wght@500;600;700&family=Roboto:wght@400;500;700&display=swap" rel="stylesheet">
<style>
:root{
  --green:#135d38;
  --green-dark:#0f4f2f;
  --gold:#cda346;
  --ink:#222222;
  --text:#7a7a7a;
  --light:#f4f4f4;
  --white:#ffffff;
}
*{box-sizing:border-box;margin:0;padding:0}
html,body{width:1200px;height:3954px;overflow:hidden}
body{position:relative;background:var(--white);font-family:"Roboto",Arial,sans-serif;color:var(--ink)}
.abs{position:absolute}
.serif{font-family:"Cinzel",Georgia,serif}

/* header */
.site-header{position:absolute;left:0;top:0;width:1200px;height:120px;border-top:5px solid var(--green);background:var(--white)}
.brand{position:absolute;left:110px;top:34px;display:flex;align-items:center;gap:14px}
.brand-mark{width:34px;height:34px;background:var(--gold)}
.brand-name{font-family:"Cinzel",Georgia,serif;font-weight:600;font-size:32px;color:var(--green);letter-spacing:1px}
.main-nav{position:absolute;top:53px;left:605px;display:flex;gap:0}
.main-nav a{position:absolute;font-weight:700;font-size:13px;color:var(--ink);text-decoration:none;white-space:nowrap}
.main-nav a.active{color:var(--gold)}
.btn{display:flex;align-items:center;justify-content:center;background:var(--gold);color:var(--white);font-weight:700;font-size:13px;text-transform:uppercase;text-decoration:none;box-shadow:5px 5px 0 -1px var(--white),5px 5px 0 0 var(--green)}
.btn-green{background:var(--green);box-shadow:none;font-size:10px}

/* hero */
.hero{position:absolute;left:0;top:120px;width:1200px;height:680px;overflow:hidden}
.hero-photo{position:absolute;inset:0;background:linear-gradient(180deg,#5a3418 0%,#a77a4e 30%,#c9a77d 48%,#8a5530 70%,#4a2c18 100%)}
.hero-title{position:absolute;left:0;width:1200px;text-align:center;font-family:"Cinzel",Georgia,serif;font-weight:600}
.hero-dots{position:absolute;top:591px;left:566px;display:flex;gap:10px}
.hero-dots span{width:8px;height:8px;border:1px solid var(--white);transform:rotate(45deg)}
.hero-dots span.on{background:var(--white)}

/* section headings */
.section-title{position:absolute;left:0;width:1200px;text-align:center;font-family:"Cinzel",Georgia,serif;font-weight:700;font-size:52px;color:var(--ink)}
.section-title em{font-style:normal;color:var(--green)}

/* rooms */
.room-card{position:absolute;top:964px;width:310px;height:428px;background:var(--white);box-shadow:0 2px 14px rgba(0,0,0,.12);text-align:center}
.room-photo{position:absolute;left:9px;top:9px;width:292px;height:207px}
.room-card h3{position:absolute;top:236px;width:100%;font-size:16px;font-weight:500;color:var(--ink)}
.room-card p{position:absolute;top:282px;left:22px;right:22px;font-size:12px;line-height:22px;color:var(--text)}
.room-card .btn{position:absolute;left:106px;top:368px;width:97px;height:34px}

/* features */
.features{position:absolute;left:0;top:1566px;width:1200px;height:404px}
.feature{position:absolute;top:110px;width:300px;text-align:center;color:var(--white)}
.feature-icon{position:absolute;top:0;left:103px;width:94px;height:94px}
.feature h3{position:absolute;top:114px;width:100%;font-size:18px;font-weight:700}
.feature p{position:absolute;top:150px;left:22px;right:22px;font-size:13px;line-height:24px}

/* testimonials */
.testimonials{position:absolute;left:0;top:1970px;width:1200px;height:565px;background:var(--light)}
.review{position:absolute;top:181px;width:310px;height:290px;background:var(--white);border-radius:8px;box-shadow:0 2px 12px rgba(0,0,0,.06);text-align:center}
.avatar{position:absolute;left:117px;top:21px;width:76px;height:76px;border-radius:50%}
.review p{position:absolute;top:118px;left:22px;right:22px;font-size:13px;line-height:25px;color:var(--text)}
.review .quote{position:absolute;font-family:Georgia,serif;font-size:96px;line-height:1;color:#e4e4e4}
.review .name{position:absolute;top:262px;width:100%;font-size:16px;font-weight:500;color:var(--gold);text-transform:uppercase}

/* gallery */
.gallery-photo{position:absolute}

/* contact */
.map{position:absolute;left:0;top:3311px;width:574px;height:446px;background:linear-gradient(135deg,#ecebe6,#e2e0d9)}
.contact{position:absolute;left:574px;top:3311px;width:626px;height:446px;background:var(--gold)}
.contact h2{position:absolute;left:78px;top:44px;font-family:"Cinzel",Georgia,serif;font-weight:600;font-size:40px;color:var(--white)}
.field{position:absolute;background:var(--white);border:0;font-size:13px;color:#888;padding:0 14px;display:flex;align-items:center;gap:8px}
.field.area{align-items:flex-start;padding-top:14px}
.field svg{flex:none}
.submit{position:absolute;left:78px;top:344px;width:153px;height:49px;background:var(--green);color:var(--white);font-weight:700;font-size:14px;display:flex;align-items:center;justify-content:center;gap:10px}
.seal{position:absolute;left:522px;top:3474px;width:120px;height:120px;border-radius:50%;background:rgba(255,255,255,.35)}
.seal span{position:absolute;left:14px;top:14px;width:92px;height:92px;border-radius:50%;background:var(--white)}

/* footer */
.site-footer{position:absolute;left:0;top:3757px;width:1200px;height:197px;background:var(--green);color:var(--white)}
.footer-nav{position:absolute;left:110px;top:80px;display:flex;gap:24px;font-size:14px;font-weight:500}
.footer-rule{position:absolute;top:115px;height:1px;background:rgba(255,255,255,.6)}
.footer-brand{position:absolute;left:486px;top:78px;display:flex;align-items:center;gap:12px}
.footer-brand .brand-mark{width:30px;height:30px;background:var(--white)}
.footer-brand .brand-name{color:var(--white);font-size:30px}
.footer-contact{position:absolute;right:110px;top:80px;font-size:14px;display:flex;align-items:center;gap:8px}
.copyright{position:absolute;left:110px;top:136px;font-size:12px}
.social{position:absolute;top:126px;width:34px;height:34px;border-radius:50%}
</style>
</head>
<body>

<header class="site-header">
  <div class="brand"><span class="brand-mark"></span><span class="brand-name">Corvena Hotel</span></div>
  <nav class="main-nav">
    <a class="active" style="left:0">HOME</a>
    <a style="left:73px">ROOMS</a>
    <a style="left:156px">GALLERY</a>
    <a style="left:248px">CONTACT</a>
  </nav>
  <a class="btn abs" style="left:962px;top:29px;width:119px;height:50px">Book Now</a>
</header>

<section class="hero">
  <div class="hero-photo" role="img" aria-label="Hotel reception desk with warm lighting and table lamps"></div>
  <h1 class="hero-title" style="top:196px;font-size:46px;color:var(--ink)">ENJOY A</h1>
  <h1 class="hero-title" style="top:253px;font-size:52px;color:var(--green)">LUXURY EXPERIENCE</h1>
  <a class="btn abs" style="left:525px;top:340px;width:147px;height:50px">Explore Now</a>
  <div class="hero-dots"><span></span><span class="on"></span><span></span><span></span></div>
  <svg class="abs" style="left:0;top:0" width="1200" height="680" viewBox="0 0 1200 680">
    <polygon points="0,600 600,532 1200,600 1200,662 600,575 0,662" fill="var(--gold)"/>
    <polygon points="0,662 600,575 1200,662 1200,668 600,680 0,668" fill="var(--green)"/>
    <polygon points="0,668 600,680 0,680" fill="var(--white)"/>
    <polygon points="1200,668 600,680 1200,680" fill="var(--white)"/>
  </svg>
</section>

<h2 class="section-title" style="top:872px">ROOM <em>TYPES</em></h2>

<article class="room-card" style="left:110px">
  <div class="room-photo" role="img" aria-label="Bright apartment bedroom with white bed" style="background:linear-gradient(135deg,#d8d2c8,#f3f1ec 55%,#a79a88)"></div>
  <h3>APARTMENT FOR 4 ADULTS</h3>
  <p>Situated on the top floor of the hotel, this fully air - conditioned apartment consists of 2 bedrooms, living room, kitchen and wooden patio.</p>
  <a class="btn btn-green">Read More</a>
</article>
<article class="room-card" style="left:445px">
  <div class="room-photo" role="img" aria-label="Superior double room with wooden screen and striped pillows" style="background:linear-gradient(135deg,#3e2a1c,#8a6a4c 55%,#d9cfc0)"></div>
  <h3>SUPERIOR DOUBLE ROOM</h3>
  <p>This spacious room features a queen size bed or a sofa that turns into a double bed. It features satellite television, a coffee machine</p>
  <a class="btn btn-green">Read More</a>
</article>
<article class="room-card" style="left:780px">
  <div class="room-photo" role="img" aria-label="Quadruple room with bed and bedside lamps" style="background:linear-gradient(135deg,#2e2418,#7d6a52 50%,#e0d8ca)"></div>
  <h3>QUADRUPLE ROOM</h3>
  <p>This more spacious room has a queen size bed and a sofa that turns into a double bed. It features satellite TV, a coffee machine</p>
  <a class="btn btn-green">Read More</a>
</article>

<a class="btn abs" style="left:520px;top:1450px;width:151px;height:46px">View All Rooms</a>

<section class="features">
  <svg class="abs" style="left:0;top:0" width="1200" height="404" viewBox="0 0 1200 404">
    <polygon points="0,46 300,0 300,404 0,404" fill="var(--green)"/>
    <polygon points="300,0 600,66 600,404 300,404" fill="var(--gold)"/>
    <polygon points="600,46 900,0 900,404 600,404" fill="var(--green)"/>
    <polygon points="900,0 1200,66 1200,404 900,404" fill="var(--gold)"/>
  </svg>

  <div class="feature" style="left:0">
    <svg class="feature-icon" viewBox="0 0 94 94"><rect x="19" y="19" width="56" height="56" transform="rotate(45 47 47)" fill="var(--gold)"/><path d="M47 33c-6 0-10 4-10 10 0 8 10 18 10 18s10-10 10-18c0-6-4-10-10-10z" fill="none" stroke="#fff" stroke-width="2"/><circle cx="47" cy="43" r="3.5" fill="none" stroke="#fff" stroke-width="2"/><ellipse cx="47" cy="62" rx="11" ry="3" fill="none" stroke="#fff" stroke-width="1.5"/></svg>
    <h3>LOCATION</h3>
    <p>Medieval city is just a few steps away, so are the beautiful beaches of Elli and Psaroupola. New market is available all around the hotel, with lots of commercial shops like Velora, Markwell, etc..</p>
  </div>
  <div class="feature" style="left:300px">
    <svg class="feature-icon" viewBox="0 0 94 94"><rect x="19" y="19" width="56" height="56" transform="rotate(45 47 47)" fill="var(--green)"/><circle cx="47" cy="45" r="10" fill="none" stroke="#fff" stroke-width="2"/><circle cx="47" cy="45" r="4" fill="none" stroke="#fff" stroke-width="2"/><path d="M47 31v4M47 55v4M33 45h4M57 45h4M37 35l3 3M57 35l-3 3M37 55l3-3M57 55l-3-3" stroke="#fff" stroke-width="2"/></svg>
    <h3>OPERATION</h3>
    <p>Famous for its friendliness, cleanliness and various amenities found only in higher category establishments. Offering American enhanced breakfast from 07:30 until 11:00 daily</p>
  </div>
  <div class="feature" style="left:600px">
    <svg class="feature-icon" viewBox="0 0 94 94"><rect x="19" y="19" width="56" height="56" transform="rotate(45 47 47)" fill="var(--gold)"/><path d="M35 58l8-14 6 4 4-10 6 6-6 14z" fill="none" stroke="#fff" stroke-width="2" stroke-linejoin="round"/><path d="M41 34l2 4M47 31v4M53 34l-2 4" stroke="#fff" stroke-width="2"/></svg>
    <h3>FRIENDLINESS</h3>
    <p>The hotel offers its services to both local and international guests either family or business type. Corvena staff acts more like family than employees as most of them have been around for so many years</p>
  </div>
  <div class="feature" style="left:900px">
    <svg class="feature-icon" viewBox="0 0 94 94"><rect x="19" y="19" width="56" height="56" transform="rotate(45 47 47)" fill="var(--green)"/><path d="M33 54a14 14 0 0 1 28 0z" fill="none" stroke="#fff" stroke-width="2"/><path d="M30 58h34M47 40v-3M44 37h6M33 36l3 3M61 36l-3 3" stroke="#fff" stroke-width="2"/></svg>
    <h3>AMENITIES</h3>
    <p>The hotel offers most modern amenities, like satellite television set, mini bar, en sure bathroom with amenities, hairdryer, safe storage area for valuables, laminated flooring, double glazed windows &amp; balcony.</p>
  </div>
</section>

<section class="testimonials">
  <h2 class="section-title" style="top:78px">OUR <em>TESTIMONIALS</em></h2>

  <article class="review" style="left:110px">
    <div class="avatar" role="img" aria-label="Guest portrait" style="background:radial-gradient(circle,#c99a7a,#6b4a36)"></div>
    <span class="quote" style="left:16px;top:96px">&ldquo;</span>
    <span class="quote" style="right:16px;top:156px">&rdquo;</span>
    <p>The Corvena is a charming little place in a perfect spot. Rooms are comfortable, very effective AC and a compact, but very good, bathroom. Cleaning staff v good. Breakfast was a very good selection...</p>
    <span class="name">Marta K</span>
  </article>
  <article class="review" style="left:445px">
    <div class="avatar" role="img" aria-label="Guest portrait" style="background:radial-gradient(circle,#d0a27e,#2f6a9a)"></div>
    <span class="quote" style="left:16px;top:96px">&ldquo;</span>
    <span class="quote" style="right:16px;top:156px">&rdquo;</span>
    <p>Stavros Welcomed us with a very generous touch, Authentic Greek Hospitality, If you want to experience a genuine village experience with the community, and savor the magnificent viewing...</p>
    <span class="name">Julien</span>
  </article>
  <article class="review" style="left:780px">
    <div class="avatar" role="img" aria-label="Guest portrait" style="background:radial-gradient(circle,#d2ab8c,#4a6f93)"></div>
    <span class="quote" style="left:16px;top:96px">&ldquo;</span>
    <span class="quote" style="right:16px;top:156px">&rdquo;</span>
    <p>The location fo the place was pretty close to the old town, the beach, bars, and restaurants, facilities were really good and staff was very friendly and kind ti help in any situation...</p>
    <span class="name">Nikos</span>
  </article>
</section>

<h2 class="section-title" style="top:2612px">OUR <em>GALLERY</em></h2>
<div class="gallery-photo" role="img" aria-label="Rooftop deck with white gazebo and loungers" style="left:110px;top:2710px;width:478px;height:232px;background:linear-gradient(180deg,#b9c7d6,#8a7157 55%,#5b4630)"></div>
<div class="gallery-photo" role="img" aria-label="Wooden fenced terrace with green plants" style="left:612px;top:2710px;width:478px;height:232px;background:linear-gradient(135deg,#3d3128,#6f7c4a 50%,#cfc7b9)"></div>
<div class="gallery-photo" role="img" aria-label="Apartment kitchen with white cabinets" style="left:110px;top:2965px;width:310px;height:231px;background:linear-gradient(135deg,#ece8e1,#c9b9a2 60%,#7c6650)"></div>
<div class="gallery-photo" role="img" aria-label="Room with balcony door and dark wood floor" style="left:445px;top:2965px;width:310px;height:231px;background:linear-gradient(180deg,#e8e6e2,#9c8d7c 55%,#3b2c22)"></div>
<div class="gallery-photo" role="img" aria-label="Bedroom with white bed and wall art" style="left:780px;top:2965px;width:310px;height:231px;background:linear-gradient(135deg,#8b7056,#e7ddd0 55%,#f7f4ef)"></div>

<div class="map" role="img" aria-label="Street map showing the hotel location in Rhodes town"></div>
<section class="contact">
  <h2>CONTACT US</h2>
  <div class="field" style="left:78px;top:137px;width:215px;height:43px"><svg width="12" height="12" viewBox="0 0 12 12"><circle cx="6" cy="3.5" r="2.8" fill="#bbb"/><path d="M1 12a5 5 0 0 1 10 0z" fill="#bbb"/></svg>First Name</div>
  <div class="field" style="left:299px;top:137px;width:217px;height:43px"><svg width="12" height="12" viewBox="0 0 12 12"><circle cx="6" cy="3.5" r="2.8" fill="#bbb"/><path d="M1 12a5 5 0 0 1 10 0z" fill="#bbb"/></svg>Last Name</div>
  <div class="field" style="left:78px;top:188px;width:215px;height:42px"><svg width="12" height="12" viewBox="0 0 12 12"><path d="M2 1l3 0 1 3-2 1a7 7 0 0 0 3 3l1-2 3 1v3c-6 0-10-4-10-9z" fill="#bbb"/></svg>Your Phone</div>
  <div class="field" style="left:299px;top:188px;width:217px;height:42px"><svg width="13" height="10" viewBox="0 0 13 10"><rect width="13" height="10" fill="#bbb"/><path d="M0 0l6.5 5L13 0" stroke="#fff" fill="none"/></svg>Your Email</div>
  <div class="field area" style="left:78px;top:238px;width:438px;height:97px"><svg width="13" height="11" viewBox="0 0 13 11"><ellipse cx="6.5" cy="5" rx="6.5" ry="5" fill="#bbb"/></svg>Message</div>
  <div class="submit">SUBMIT <svg width="16" height="14" viewBox="0 0 16 14"><path d="M0 7l16-7-4 14-4-5z" fill="#fff"/></svg></div>
</section>
<div class="seal"><span></span></div>

<footer class="site-footer">
  <nav class="footer-nav"><span>HOME</span><span>ROOMS</span><span>GALLERY</span><span>CONTACT</span></nav>
  <div class="footer-rule" style="left:110px;width:344px"></div>
  <div class="footer-rule" style="left:746px;width:344px"></div>
  <div class="footer-brand"><span class="brand-mark"></span><span class="brand-name">Corvena Hotel</span></div>
  <div class="footer-contact">
    <svg width="13" height="13" viewBox="0 0 12 12"><path d="M2 1l3 0 1 3-2 1a7 7 0 0 0 3 3l1-2 3 1v3c-6 0-10-4-10-9z" fill="var(--gold)"/></svg>
    <span>(+30) 22410 55314</span><span>|</span>
    <svg width="14" height="11" viewBox="0 0 13 10"><rect width="13" height="10" fill="var(--gold)"/><path d="M0 0l6.5 5L13 0" stroke="var(--green)" fill="none"/></svg>
    <span>info@corvenahotel.gr</span>
  </div>
  <div class="copyright">© 2022 CORVENA HOTEL &nbsp;|&nbsp; All Rights Reserved</div>
  <span class="social" style="left:1014px;background:var(--gold)"></span>
  <span class="social" style="left:1054px;background:var(--white)"></span>
</footer>

</body>
</html>
```